Social Media Graphics - Oakline Push REVISED

Create 6-7 individual social media graphics (square size) to encourage folks to join our online course called:

The Harvest Ledger Circle
How to Launch a Multi-Million Business From Scratch
Sign Up Today!

IMPORTANT: Make the largest and most prominent text on the graphic be: How to Launch a Multi-Million Business From Scratch

For the color scheme of the graphics, let's try a blue color palette; make sure the graphics appeal to both men and women

Make sure each graphic contains 1 of the 3 pics attached (crop pic as needed); and make sure one of the graphics is all TEXT only.

Target Market(s)

men and women looking to start a business

Industry/Entity Type

Entrepreneurship

Colors
0054AA
0677BA
7BADD7
CADEEF
E8F1F8

Requirements
Must have
• All the text and use the 3 pics provided; one graphic can be all text; Simple, modern design that's easy to read

```html
<!DOCTYPE html>
<html lang="en">
<head>
<meta charset="UTF-8">
<title>The Harvest Ledger Circle – How to Launch a Multi-Million Business From Scratch</title>
<link href="https://fonts.googleapis.com/css2?family=League+Spartan:wght@700&family=Open+Sans:wght@700&display=swap" rel="stylesheet">
<style>
  :root {
    --sky: #E8F1F8;
    --royal: #0048AD;
    --ink: #14213D;
    --night-top: #0B1C66;
    --night-bottom: #040A2E;
    --star: #4FA3E8;
    --white: #F4F8FC;
  }
  html, body {
    margin: 0;
    padding: 0;
    width: 1200px;
    height: 1200px;
    overflow: hidden;
    background: var(--sky);
  }
  .post {
    position: relative;
    width: 1200px;
    height: 1200px;
    overflow: hidden;
    background: var(--sky);
  }
  .backdrop {
    position: absolute;
    inset: 0;
  }
  .course-name {
    position: absolute;
    top: 140px;
    left: 0;
    width: 1200px;
    margin: 0;
    text-align: center;
    font-family: "Open Sans", Arial, sans-serif;
    font-weight: 700;
    font-size: 46px;
    letter-spacing: 2px;
    color: var(--ink);
    text-transform: uppercase;
  }
  .headline {
    position: absolute;
    top: 212px;
    left: 0;
    width: 1200px;
    margin: 0;
    text-align: center;
    font-family: "League Spartan", "Arial Black", sans-serif;
    font-weight: 700;
    font-size: 112px;
    line-height: 114px;
    color: var(--royal);
    text-transform: uppercase;
  }
  .hosts-photo {
    position: absolute;
    left: 242px;
    top: 712px;
    width: 710px;
    height: 488px;
    border-radius: 240px 240px 0 0;
    background: radial-gradient(ellipse at 50% 35%, #6b4a3a 0%, #2b2430 45%, #162a55 80%, rgba(22,42,85,0) 100%);
  }
  .cta {
    position: absolute;
    left: 900px;
    top: 940px;
    width: 250px;
    margin: 0;
    text-align: center;
    font-family: "Open Sans", Arial, sans-serif;
    font-weight: 700;
    font-size: 56px;
    line-height: 80px;
    color: var(--white);
    text-transform: uppercase;
  }
</style>
</head>
<body>
  <div class="post">
    <svg class="backdrop" width="1200" height="1200" viewBox="0 0 1200 1200" aria-hidden="true">
      <defs>
        <linearGradient id="night" x1="0" y1="0" x2="0.3" y2="1">
          <stop offset="0" stop-color="var(--night-top)"/>
          <stop offset="1" stop-color="var(--night-bottom)"/>
        </linearGradient>
      </defs>
      <polygon class="top-notch" points="506,0 745,0 625,118" fill="var(--royal)"/>
      <polygon class="night-field" points="0,484 600,1084 1200,470 1200,1200 0,1200" fill="url(#night)"/>
      <g class="stars" fill="var(--star)">
        <circle cx="38" cy="632" r="2.5" opacity="0.7"/>
        <circle cx="118" cy="750" r="2" opacity="0.6"/>
        <circle cx="135" cy="760" r="2.5" opacity="0.8"/>
        <circle cx="60" cy="945" r="1.8" opacity="0.5"/>
        <circle cx="112" cy="1035" r="4" opacity="0.8"/>
        <circle cx="215" cy="855" r="2" opacity="0.6"/>
        <circle cx="200" cy="1000" r="3" opacity="0.6"/>
        <circle cx="1132" cy="600" r="3" opacity="0.9"/>
        <circle cx="1136" cy="622" r="2.5" opacity="0.8"/>
        <circle cx="1012" cy="712" r="3" opacity="0.8"/>
        <circle cx="1120" cy="918" r="2.5" opacity="0.7"/>
        <circle cx="1150" cy="900" r="2" opacity="0.6"/>
        <circle cx="1045" cy="1045" r="2" opacity="0.5"/>
        <circle cx="980" cy="840" r="1.8" opacity="0.5"/>
      </g>
    </svg>

    <p class="course-name">The Harvest Ledger Circle</p>
    <h1 class="headline">How to Launch<br>A Multi-Million<br>Business From<br>Scratch</h1>

    <div class="hosts-photo" role="img" aria-label="Photo of the two course hosts, a man in a black turtleneck and a woman in a denim jacket, smiling"></div>

    <p class="cta">Sign Up<br>Today</p>
  </div>
</body>
</html>
```